Drone service provider needs a brilliant web design

I need a responsive web design for a new drone service company. Pelham Drone Solutions provides turnkey solutions to capture, process, and deliver actionable aerial data to customers. The design should communicate a professional company that is safe, legal and insured. I included our logo design and business card designs for reference.
*content to be supplied after design selected

Target Market(s)

We serve telecommunications, construction, government, utility infrastructure, insurance and other industries.

Industry/Entity Type

Industrial

Number of Pages Required

5+ page

Colors

Designer to choose colors to be used in the design.

Requirements
Must have
• The design should highlight professional services to include Inspections, Mapping, Consulting and Training. The site should include aerial images and video to compliment the services offered. The landing page must include following sections in order: HOME, SERVICES, ABOUT, DEMO REEL, CLIENTS, CONTACT FORM, and social media buttons (Facebook, LinkedIn, Twitter, YouTube, Instagram). Contact: 615-382-9041 info@pelhamdronesolutions-example.com Smyrna, TN
• Sitemap:
• 6 pages: Home, Inspections, Mapping, Training, Consulting, About
• HOME (Landing Page)
• • Header with logo and tab links (Home, Services, About, Contact)
• • 'CAPTURE. PROCESS. DELIVER.' tagline and 'CONTACT US' button displayed within aerial image of drone over city or construction site
• • Services section with icons, text and read more link to page
• • About section with photo and text with three icons for SAFE. LEGAL. INSURED.
• • Demo reel
• • Clients logos shown scrolling horizontally
• • Contact form
• • Footer with logo, phone, email, social media buttons
• SERVICES (4 different pages)
• • Inspections
• • Mapping
• • Consulting
• • Training
• ABOUT page
• • Company
• • Partners
• • Certifications & Associations
• • Careers
• CONTACT linked to bottom of landing page
• Would you like to receive the newsletter? Yes or No Drop-down list
Nice to have
• Photos of KVR Marlin or Corvex inspecting infrastructure, buildings, construction sites, etc. A photo of one or two pilots in vest and helmet. Free stock photos preferred but would purchase the right photo that's more relevant.
• website references:
• https://www.quillrotor-example.com/
• https://www.brentfieldworks-example.com/services
• https://www.tomaro-example.com/
• http://gantrymetric-example.com/
• http://lumbrook-example.com/
• http://fennotics-example.com/
• https://www.grebe-example.io/
Should not have
• not an aerial photography or videography service business, no blog or newsletter

```html
<!DOCTYPE html>
<html lang="en">
<head>
<meta charset="utf-8">
<title>Pelham Drone Solutions</title>
<link href="https://fonts.googleapis.com/css2?family=Montserrat:wght@600;700;800&family=Open+Sans:wght@400;600;700&display=swap" rel="stylesheet">
<style>
:root{
  --blue:#1b8fd2;
  --blue-dark:#1478b4;
  --ink:#2a2a2a;
  --text:#444;
  --muted:#8a8a8a;
  --grey-bg:#ececec;
  --white:#fff;
}
*{box-sizing:border-box;margin:0;padding:0}
html,body{width:1200px;height:3905px;overflow:hidden}
body{position:relative;background:var(--white);font-family:"Open Sans",Arial,sans-serif;color:var(--text)}
.abs{position:absolute}
.heading{font-family:"Montserrat",Arial,sans-serif}

/* header */
.site-header{left:0;top:0;width:1200px;height:117px;background:var(--blue);z-index:5}
.main-nav{left:99px;top:44px;display:flex;gap:44px;font:600 17px "Montserrat",Arial,sans-serif;color:var(--white)}
.logo-tab{left:420px;top:0;width:360px;height:117px;z-index:6}
.logo-name{left:0;top:28px;width:360px;text-align:center;font:800 42px "Montserrat",Arial,sans-serif;color:var(--ink);letter-spacing:1px}
.logo-sub{left:0;top:78px;width:360px;text-align:center;font:700 15px "Montserrat",Arial,sans-serif;color:var(--ink);letter-spacing:4px}
.social{display:flex;gap:10px}
.social span{width:36px;height:36px;border:2px solid var(--white);border-radius:50%;display:block}
.header-social{left:875px;top:40px}

/* hero */
.hero-photo{left:0;top:117px;width:1200px;height:600px;background:linear-gradient(180deg,#8c98a4 0%,#6d7a84 40%,#5b5a55 75%,#6b5c4b 100%)}
.hero-title{left:99px;top:238px;font:800 57px/1.12 "Montserrat",Arial,sans-serif;color:var(--white)}
.btn-contact{left:99px;top:442px;width:146px;height:52px;background:var(--white);border-radius:6px;font:600 17px "Open Sans",Arial,sans-serif;color:var(--blue);display:flex;align-items:center;justify-content:center}
.hero-arrows{left:99px;top:538px}
.hero-wave{left:0;top:560px;width:1200px;height:170px}

/* services */
.section-title{width:1200px;left:0;text-align:center;font:700 30px "Montserrat",Arial,sans-serif;color:var(--blue)}
.title-rule{width:80px;height:3px;background:var(--blue);left:560px}
.service{width:240px;text-align:center}
.service-icon{width:104px;height:104px;border:3px solid var(--blue);border-radius:50%;margin:0 auto;display:flex;align-items:center;justify-content:center}
.service-name{margin-top:26px;font:700 18px "Montserrat",Arial,sans-serif;color:var(--ink);letter-spacing:3px}
.service-desc{margin-top:12px;font:400 13px/1.7 "Open Sans",Arial,sans-serif;color:var(--muted);height:60px}
.read-more{margin-top:42px;font:600 15px "Open Sans",Arial,sans-serif;color:var(--blue)}

/* about */
.about-band{left:0;top:1205px;width:1200px;height:640px}
.about-photo{left:99px;top:1346px;width:461px;height:356px;background:linear-gradient(135deg,#c9d4dc 0%,#9aa7b1 50%,#6f7d55 100%)}
.about-title{left:607px;top:1350px;font:700 30px "Montserrat",Arial,sans-serif;color:var(--white)}
.about-copy{left:607px;top:1412px;width:494px;font:400 13.5px/1.75 "Open Sans",Arial,sans-serif;color:#e6e6e6;text-align:justify}
.pillar{width:130px;text-align:center;color:var(--white)}
.pillar-label{margin-top:14px;font:700 21px "Montserrat",Arial,sans-serif}

/* video */
.video{left:99px;top:1929px;width:997px;height:411px;border:3px solid #555;background:linear-gradient(160deg,#6f9a4c 0%,#4f7d35 55%,#3e6a2c 100%)}
.play{left:548px;top:2106px}

/* partners */
.partners{left:0;top:2421px;width:1200px;height:430px;background:var(--grey-bg)}
.partner-card{width:226px;height:114px;background:var(--white);border:1px solid #cfcfcf;border-radius:4px;display:flex;align-items:center;justify-content:center}
.partner-mark{width:110px;height:38px;background:#d9d9d9;border-radius:4px}
.partner-name{width:226px;text-align:center;font:700 15px "Open Sans",Arial,sans-serif;color:var(--blue)}
.partner-url{width:226px;text-align:center;font:600 13px "Open Sans",Arial,sans-serif;color:var(--ink);text-decoration:underline}

/* contact */
.contact{left:0;top:2851px;width:1200px;height:620px;background:linear-gradient(135deg,#2196da,#1883c4)}
.contact-title{color:var(--white)}
.field{border:2px solid var(--white);border-radius:7px;height:49px;padding:14px 14px;font:600 14px "Open Sans",Arial,sans-serif;color:var(--white)}
.newsletter-q{left:614px;top:3143px;font:600 14px "Open Sans",Arial,sans-serif;color:var(--white)}
.select{left:929px;top:3129px;width:146px;height:49px;background:var(--white);border-radius:7px;padding:14px;font:600 14px "Open Sans",Arial,sans-serif;color:var(--ink)}
.btn-submit{left:541px;top:3327px;width:120px;height:49px;background:var(--white);border-radius:7px;font:600 15px "Open Sans",Arial,sans-serif;color:var(--blue);display:flex;align-items:center;justify-content:center}

/* footer */
.footer-wave{left:0;top:3370px;width:1200px;height:140px}
.footer{left:0;top:3505px;width:1200px;height:400px;background:var(--ink)}
.footer-logo{left:0;top:3578px;width:1200px;text-align:center;color:var(--white)}
.footer-logo .logo-word{font:800 38px "Montserrat",Arial,sans-serif;letter-spacing:1px;display:block}
.footer-logo .logo-tag{font:700 13px "Montserrat",Arial,sans-serif;letter-spacing:4px}
.footer-contact{left:0;top:3690px;width:1200px;display:flex;justify-content:center;gap:40px;font:400 19px "Open Sans",Arial,sans-serif;color:var(--white)}
.footer-contact span{display:flex;align-items:center;gap:10px}
.footer-nav{left:0;top:3770px;width:1200px;display:flex;justify-content:center;gap:48px;font:600 14px "Montserrat",Arial,sans-serif;color:var(--white)}
.footer-rule{left:99px;top:3826px;width:997px;height:1px;background:#777}
.copyright{left:99px;top:3858px;font:400 14px "Open Sans",Arial,sans-serif;color:var(--white)}
.footer-social{left:916px;top:3848px}
.footer-social span{width:34px;height:34px}
</style>
</head>
<body>

<header class="abs site-header">
  <nav class="abs main-nav"><span>HOME</span><span>SERVICES</span><span>ABOUT</span></nav>
  <div class="abs header-social social" aria-label="Social media links"><span></span><span></span><span></span><span></span><span></span></div>
</header>
<div class="abs logo-tab">
  <svg class="abs" style="left:0;top:0" width="360" height="117" viewBox="0 0 360 117"><path d="M0 0 H360 L320 117 H40 Z" fill="#fff"/></svg>
  <div class="abs logo-name">PELHAM</div>
  <div class="abs logo-sub">DRONE SOLUTIONS</div>
</div>

<section>
  <div class="abs hero-photo" role="img" aria-label="Aerial photo of a drone flying over a city construction site by the harbour"></div>
  <h1 class="abs hero-title">CAPTURE.<br>PROCESS.<br>DELIVER.</h1>
  <div class="abs btn-contact">Contact Us</div>
  <svg class="abs hero-arrows" width="70" height="30" viewBox="0 0 70 30" aria-hidden="true">
    <path d="M26 15 H4 M13 6 L4 15 L13 24" stroke="#fff" stroke-width="4" fill="none"/>
    <path d="M40 15 H62 M53 6 L62 15 L53 24" stroke="#fff" stroke-width="4" fill="none"/>
  </svg>
  <svg class="abs hero-wave" viewBox="0 0 1200 170" preserveAspectRatio="none" aria-hidden="true">
    <path d="M0 140 C300 150 700 40 1200 20 V170 H0 Z" fill="#1b8fd2"/>
    <path d="M0 160 C350 160 720 70 1200 52 V170 H0 Z" fill="#fff"/>
  </svg>
</section>

<section>
  <h2 class="abs section-title" style="top:742px">OUR SERVICES</h2>
  <div class="abs title-rule" style="top:800px"></div>

  <div class="abs service" style="left:86px;top:859px">
    <div class="service-icon"><svg width="50" height="50" viewBox="0 0 50 50"><rect x="10" y="5" width="30" height="40" rx="3" fill="#1b8fd2"/><path d="M16 16H34M16 24H34M16 32H28" stroke="#fff" stroke-width="3"/></svg></div>
    <div class="service-name">INSPECTIONS</div>
    <div class="service-desc">Power Utilities, Infrastructure, Cell Tower, Roof, Property</div>
    <div class="read-more">Read More &gt;</div>
  </div>
  <div class="abs service" style="left:343px;top:859px">
    <div class="service-icon"><svg width="50" height="50" viewBox="0 0 50 50"><path d="M6 10 L18 5 L32 10 L44 5 V40 L32 45 L18 40 L6 45 Z" fill="none" stroke="#1b8fd2" stroke-width="3"/><path d="M18 5V40M32 10V45" stroke="#1b8fd2" stroke-width="3"/></svg></div>
    <div class="service-name">MAPPING</div>
    <div class="service-desc">Construction, Volumetric Measurement, Orthomosaic, 3D Model, Terrain Model</div>
    <div class="read-more">Read More &gt;</div>
  </div>
  <div class="abs service" style="left:601px;top:859px">
    <div class="service-icon"><svg width="50" height="50" viewBox="0 0 50 50"><circle cx="14" cy="12" r="6" fill="#1b8fd2"/><circle cx="36" cy="12" r="6" fill="#1b8fd2"/><path d="M4 30 Q14 18 24 30 Z M26 30 Q36 18 46 30 Z" fill="#1b8fd2"/><rect x="4" y="32" width="42" height="5" fill="#1b8fd2"/><path d="M12 37V46M38 37V46" stroke="#1b8fd2" stroke-width="3"/></svg></div>
    <div class="service-name">CONSULTING</div>
    <div class="service-desc">Requirements, Regulations, Solutions, Equipment, Manuals, Business Development</div>
    <div class="read-more">Read More &gt;</div>
  </div>
  <div class="abs service" style="left:859px;top:859px">
    <div class="service-icon"><svg width="50" height="50" viewBox="0 0 50 50"><rect x="18" y="6" width="28" height="22" fill="none" stroke="#1b8fd2" stroke-width="3"/><circle cx="10" cy="16" r="5" fill="#1b8fd2"/><path d="M4 44 V28 Q10 22 16 28 V44 Z" fill="#1b8fd2"/><path d="M14 28 L24 20" stroke="#1b8fd2" stroke-width="3"/><path d="M32 28V44M26 44H38" stroke="#1b8fd2" stroke-width="3"/></svg></div>
    <div class="service-name">TRAINING</div>
    <div class="service-desc">FAA Part 107 Exam Prep, Flight Operations, Risk Management, Fleet Management</div>
    <div class="read-more">Read More &gt;</div>
  </div>
</section>

<section>
  <svg class="abs about-band" viewBox="0 0 1200 640" preserveAspectRatio="none" aria-hidden="true">
    <path d="M0 70 Q600 -60 1200 70 V560 Q600 700 0 560 Z" fill="#2a2a2a"/>
  </svg>
  <div class="abs about-photo" role="img" aria-label="Drone pilot in safety vest and helmet flying a drone beside high-rise buildings"></div>
  <h2 class="abs about-title">About Pelham Drone Solutions</h2>
  <p class="abs about-copy">Pelham Drone Solutions provides your business with the critical data it needs to increase productivity, reduce risk and costs, and protect workers. Our team is certified, insured and operates safely in accordance with FAA regulations. We offer a suite of solutions leveraging the latest technology in unmanned aerial systems. Our goal is to safely and quickly deliver cost-efficient, actionable data to our customers.</p>

  <div class="abs pillar" style="left:573px;top:1588px">
    <svg width="60" height="62" viewBox="0 0 60 62"><path d="M30 3 L54 12 V30 Q54 50 30 59 Q6 50 6 30 V12 Z" fill="none" stroke="#fff" stroke-width="4"/><path d="M19 31 L27 39 L42 23" fill="none" stroke="#fff" stroke-width="5"/></svg>
    <div class="pillar-label">SAFE</div>
  </div>
  <div class="abs pillar" style="left:750px;top:1588px">
    <svg width="60" height="62" viewBox="0 0 60 62"><rect x="18" y="4" width="26" height="14" rx="2" transform="rotate(40 31 11)" fill="#fff"/><path d="M28 20 L8 44" stroke="#fff" stroke-width="6"/><rect x="24" y="50" width="32" height="8" fill="#fff"/></svg>
    <div class="pillar-label">LEGAL</div>
  </div>
  <div class="abs pillar" style="left:919px;top:1588px">
    <svg width="60" height="62" viewBox="0 0 60 62"><path d="M4 30 Q30 -4 56 30 Q49 24 43 30 Q36 24 30 30 Q24 24 17 30 Q11 24 4 30 Z" fill="#fff"/><path d="M30 30 V52 Q30 58 24 56" fill="none" stroke="#fff" stroke-width="4"/></svg>
    <div class="pillar-label">INSURED</div>
  </div>
</section>

<section>
  <div class="abs video" role="img" aria-label="Demo reel: drone surveying green farm fields with a tablet showing the mapped area"></div>
  <svg class="abs play" width="100" height="100" viewBox="0 0 100 100" aria-hidden="true">
    <circle cx="50" cy="50" r="29" fill="none" stroke="#fff" stroke-width="5"/>
    <path d="M43 36 L64 50 L43 64 Z" fill="#fff"/>
  </svg>
</section>

<section>
  <div class="abs partners"></div>
  <h2 class="abs section-title" style="top:2480px">PARTNERS</h2>
  <div class="abs title-rule" style="top:2530px"></div>

  <div class="abs partner-card" style="left:185px;top:2598px"><div class="partner-mark"></div></div>
  <div class="abs partner-name" style="left:185px;top:2735px">Grebe</div>
  <div class="abs partner-url" style="left:185px;top:2760px">https://www.grebe-example.io/</div>

  <div class="abs partner-card" style="left:487px;top:2598px"><div class="partner-mark"></div></div>
  <div class="abs partner-name" style="left:487px;top:2735px">Kestrelway</div>
  <div class="abs partner-url" style="left:487px;top:2760px">https://kestrelway-example.io/</div>

  <div class="abs partner-card" style="left:789px;top:2598px"><div class="partner-mark"></div></div>
  <div class="abs partner-name" style="left:789px;top:2735px">Vantix3D</div>
  <div class="abs partner-url" style="left:789px;top:2760px">https://vantix3d-example.com/</div>
</section>

<section>
  <div class="abs contact"></div>
  <h2 class="abs section-title contact-title" style="top:2928px">CONTACT FORM</h2>
  <div class="abs title-rule" style="top:2980px;background:#fff"></div>

  <div class="abs field" style="left:125px;top:3061px;width:461px">Name</div>
  <div class="abs field" style="left:614px;top:3061px;width:461px">Phone Number</div>
  <div class="abs field" style="left:125px;top:3129px;width:461px">Email Address</div>
  <div class="abs newsletter-q">Would you like to receive the newsletter?</div>
  <div class="abs select">Yes
    <svg class="abs" style="right:14px;top:21px" width="12" height="8" viewBox="0 0 12 8"><path d="M0 0H12L6 8Z" fill="#1b8fd2"/></svg>
  </div>
  <div class="abs field" style="left:125px;top:3197px;width:950px;height:101px">Message</div>
  <div class="abs btn-submit">Submit</div>
</section>

<footer>
  <svg class="abs footer-wave" viewBox="0 0 1200 140" preserveAspectRatio="none" aria-hidden="true">
    <path d="M0 10 Q500 130 1200 50 V140 H0 Z" fill="#fff"/>
    <path d="M0 80 Q600 110 1200 40 V140 H0 Z" fill="#1b8fd2"/>
    <path d="M0 105 Q600 125 1200 60 V140 H0 Z" fill="#2a2a2a"/>
  </svg>
  <div class="abs footer"></div>
  <div class="abs footer-logo"><span class="logo-word">PELHAM</span><span class="logo-tag">DRONE SOLUTIONS</span></div>
  <div class="abs footer-contact">
    <span><svg width="34" height="34" viewBox="0 0 34 34"><circle cx="17" cy="17" r="15" fill="none" stroke="#fff" stroke-width="2"/><rect x="9" y="11" width="16" height="12" fill="none" stroke="#fff" stroke-width="2"/><path d="M9 11 L17 18 L25 11" fill="none" stroke="#fff" stroke-width="2"/></svg>info@pelhamdronesolutions-example.com</span>
    <span><svg width="34" height="34" viewBox="0 0 34 34"><circle cx="17" cy="17" r="15" fill="none" stroke="#fff" stroke-width="2"/><path d="M11 9 L15 9 L16 14 L14 16 Q16 20 19 21 L21 19 L25 20 V24 Q17 25 12 19 Q9 14 11 9Z" fill="#fff"/></svg>615-382-9041</span>
  </div>
  <nav class="abs footer-nav"><span>HOME</span><span>|</span><span>SERVICES</span><span>|</span><span>ABOUT</span><span>|</span><span>CONTACT US</span></nav>
  <div class="abs footer-rule"></div>
  <div class="abs copyright">Copyright © 2018 Pelham Drone Solutions. All Right Reserved</div>
  <div class="abs footer-social social" aria-label="Social media links"><span></span><span></span><span></span><span></span><span></span></div>
</footer>

</body>
</html>
```